Natural Medicine & Health/Fitness Coaching studio requires web page

Require a innovative web page for a studio that coaches clients to better health, nutrition and fitness. The studio compromises of Clinical Nutritionists, Naturopaths, Rehab Trainers, Personal Trainers and Sport Coaches. Would like to see earthy but bold designs emphasizing nutritional health and athletic performance.
Updates

Design only launched today.

Target Market(s)

All genders from 20's to 60's, as well as families

Industry/Entity Type

Nutritionist

Coding

Coded - Design and coding required

Number of Pages Required

3 page

Colors
abd037
3277b5
fbee3d
fece3e
33b8a4
f04a50

Requirements
Must have
• Online booking system, ability to message
• Home page
• Coaching/Fitness page
• Nutritional Medicine page
• Must be suitable for both Fitness and Nutrition

```html
<!DOCTYPE html>
<html lang="en">
<head>
<meta charset="utf-8">
<title>Vital Peak – Nutritional Therapy</title>
<link href="https://fonts.googleapis.com/css2?family=Montserrat:wght@400;500;600;700;800&family=Open+Sans:wght@400;600&family=Lato:wght@400;700&display=swap" rel="stylesheet">
<style>
:root{
  --green:#abd037;
  --leaf:#7cb82f;
  --emerald:#0a9e4f;
  --teal:#0b8a7a;
  --blue:#1d6fa8;
  --navy:#1b5a8c;
  --dark:#1f2320;
  --ink:#333;
  --grey:#f2f2f2;
  --white:#fff;
}
*{box-sizing:border-box;margin:0;padding:0}
html,body{width:1200px;height:3273px;overflow:hidden}
body{font-family:"Open Sans",sans-serif;color:var(--ink);background:var(--white);position:relative}
.abs{position:absolute}
h1,h2,h3,.nav,.btn{font-family:"Montserrat",sans-serif}

/* header / hero */
.hero{left:0;top:0;width:1200px;height:578px;background:linear-gradient(90deg,#fafafa 0%,#eef1f3 55%,#e3e8ec 100%)}
.brand{left:92px;top:34px;display:flex;align-items:center;gap:12px}
.brand-dot{width:22px;height:22px;border-radius:50%;background:var(--blue)}
.brand-name{font-family:"Montserrat",sans-serif;font-weight:600;font-size:44px;color:var(--leaf);line-height:1}
.brand-tag{left:160px;top:88px;font-size:15px;color:var(--leaf);font-family:"Montserrat",sans-serif}
.nav{left:505px;top:56px;display:flex;gap:0;font-size:15px;color:#333}
.nav a{color:#333;text-decoration:none;padding:6px 12px;margin-right:8px}
.nav a.active{border:2px solid var(--teal);color:var(--navy);font-weight:700}
.hero-photo{left:420px;top:130px;width:700px;height:448px;background:radial-gradient(ellipse at 55% 40%,#f6f6f6 0%,#dfe5ea 60%,#d2dbe2 100%)}
.hero-kicker{left:92px;top:208px;font-size:31px;font-weight:500;color:#555;letter-spacing:.5px}
.hero-title{left:90px;top:258px;font-size:47px;font-weight:600;color:var(--navy);letter-spacing:.5px}
.hero-text{left:92px;top:320px;width:300px;font-size:14px;line-height:28px;color:#444}
.btn{display:inline-block;font-size:14px;font-weight:600;padding:8px 20px;text-decoration:none}
.btn-hero{left:92px;top:399px;border:2px solid var(--leaf);color:var(--leaf)}

/* about */
.about{left:0;top:578px;width:1200px;height:535px;background:linear-gradient(100deg,#2a2f2a 0%,#1c211d 50%,#2d302a 100%)}
.video{left:92px;top:711px;width:467px;height:315px;background:linear-gradient(135deg,#8da04a,#5e7a2c 60%,#6a7d3a)}
.play{left:280px;top:822px}
.about-title{left:600px;top:705px;font-size:29px;font-weight:800;color:var(--white)}
.about-title span{color:var(--emerald)}
.about-text{left:600px;top:790px;width:540px;font-size:14px;line-height:46px;color:#eee}
.btn-light{border:2px solid var(--white);color:var(--white)}
.btn-about{left:600px;top:980px}

/* coaching */
.coaching{left:0;top:1113px;width:1200px;height:567px;background:linear-gradient(120deg,#0bae4c 0%,#069a5f 45%,#0c7f8e 75%,#1a6ea8 100%)}
.section-title{font-size:28px;font-weight:700;text-align:center;width:1200px;left:0}
.coach-title{top:1206px;color:var(--white)}
.coach-text{left:92px;top:1328px;width:510px;font-size:14px;line-height:37px;color:var(--white)}
.btn-coach{left:92px;top:1503px}
.coach-photo{left:665px;top:1255px;width:405px;height:425px;background:linear-gradient(180deg,#13866f 0%,#1c5f86 60%,#23303f 100%);border-radius:160px 160px 0 0}

/* services */
.services{left:0;top:1680px;width:1200px;height:458px;background:var(--grey)}
.serv-title{top:1730px;color:#222}
.serv{width:300px;text-align:center;top:1796px}
.serv-img{width:188px;height:188px;border-radius:50%;margin:0 auto;border:5px solid var(--navy);box-shadow:0 0 0 4px var(--leaf) inset}
.serv-label{font-family:"Lato",sans-serif;font-size:20px;line-height:33px;color:#333;margin-top:32px}

/* testimonial */
.testi{left:0;top:2080px;width:1200px;height:560px}
.avatar{left:538px;top:2170px;width:124px;height:134px}
.t-name{left:0;width:1200px;top:2314px;text-align:center;font-family:"Lato",sans-serif;font-weight:700;font-size:20px;color:var(--white)}
.t-loc{left:0;width:1200px;top:2345px;text-align:center;font-family:"Lato",sans-serif;font-size:15px;color:#e8f2f5}
.t-quote{left:230px;width:740px;top:2395px;text-align:center;font-size:22px;line-height:34px;color:var(--white)}
.dots{left:534px;top:2532px;display:flex;gap:26px;align-items:center}
.dots span{width:5px;height:5px;border-radius:50%;background:rgba(255,255,255,.5)}
.dots span.on{background:var(--white)}

/* booking */
.book{left:0;top:2607px;width:1200px;height:572px;background:linear-gradient(90deg,#2d2218 0%,#1e1712 50%,#2a2019 100%)}
.book-title{top:2668px;color:var(--white)}
.form{left:240px;top:2771px;width:369px;height:325px;background:linear-gradient(150deg,#0aa35b 0%,#0a8a7b 55%,#1870a5 100%);padding:30px 34px}
.field{position:relative;height:44px;border-bottom:1.5px solid rgba(255,255,255,.85);font-family:"Montserrat",sans-serif;font-size:12px;color:var(--white);padding-top:10px;margin-bottom:0}
.field svg{position:absolute;right:4px;top:10px}
.field.msg{height:70px}
.submit{margin-top:20px;display:inline-block;background:var(--white);color:var(--teal);font-family:"Montserrat",sans-serif;font-size:15px;font-weight:600;padding:10px 48px}
.contact{left:692px;top:2763px;color:var(--white)}
.contact h3{font-size:26px;font-weight:600;margin-bottom:22px}
.c-label{font-family:"Montserrat",sans-serif;font-size:12px;font-weight:600;margin-top:14px}
.c-val{font-family:"Montserrat",sans-serif;font-size:15px;margin-top:2px}
.social{display:flex;gap:24px;margin-top:18px}
.social span{width:16px;height:16px;border-radius:50%;background:var(--white)}

/* footer */
.footer{left:0;top:3179px;width:1200px;height:94px;background:var(--grey)}
.footer p{position:absolute;width:1200px;top:43px;text-align:center;font-size:11px;color:#555}
</style>
</head>
<body>

<!-- Hero -->
<section class="abs hero">
  <div class="abs hero-photo" role="img" aria-label="Smiling nutritionist in a white coat at a laptop with floating food photo tiles"></div>
</section>
<div class="abs brand"><span class="brand-dot"></span><span class="brand-name">Vital Peak</span></div>
<div class="abs brand-tag">Nutritional Therapy</div>
<nav class="abs nav">
  <a class="active" href="#">HOME</a><a href="#">ABOUT US</a><a href="#">COACHING</a><a href="#">FITNESS</a><a href="#">NUTRITION</a><a href="#">CONTACT US</a>
</nav>
<h2 class="abs hero-kicker">WELCOME TO</h2>
<h1 class="abs hero-title">VITAL PEAK</h1>
<p class="abs hero-text">Lorem ipsum dolor sit amet, consectetur adipiscing elit, sed do eiusmod tempor</p>
<a class="abs btn btn-hero" href="#">Read more</a>

<!-- About -->
<section class="abs about" role="img" aria-label="Dark backdrop of healthy food on a table"></section>
<svg class="abs" style="left:0;top:578px" width="1200" height="535" viewBox="0 0 1200 535">
  <polygon points="0,0 560,0 0,105" fill="#0a9e4f"/>
  <polygon points="0,0 300,0 0,62" fill="#0b7f4a"/>
  <polygon points="620,525 1200,440 1200,535 560,535" fill="#2ea6dd"/>
</svg>
<div class="abs video" role="img" aria-label="Fruit, vegetables, dumbbells and skipping rope on a wooden table"></div>
<svg class="abs play" width="92" height="92" viewBox="0 0 92 92" aria-label="Play video">
  <circle cx="46" cy="46" r="41" fill="none" stroke="#fff" stroke-width="6"/>
  <polygon points="36,26 36,66 68,46" fill="#fff"/>
</svg>
<h2 class="abs about-title">ABOUT <span>VITAL PEAK</span></h2>
<p class="abs about-text">Sed ut perspiciatis unde omnis iste natus error sit voluptatem accusantium doloremque laudantium, totam rem aperiam, eaque ipsa quae ab illo inventore veritatis et quasi architecto beatae vitae dicta sunt explicabo.</p>
<a class="abs btn btn-light btn-about" href="#">READ MORE</a>

<!-- Coaching -->
<section class="abs coaching"></section>
<svg class="abs" style="left:0;top:1100px" width="1200" height="60" viewBox="0 0 1200 60">
  <polygon points="620,38 1200,0 1200,24 700,40" fill="#2ea6dd"/>
</svg>
<h2 class="abs section-title coach-title">COACHING</h2>
<p class="abs coach-text">Sed ut perspiciatis unde omnis iste natus error sit voluptatem accusantium doloremque laudantium, totam rem aperiam, eaque ipsa quae ab illo inventore veritatis et quasi architecto beatae vitae dicta sunt explicabo. Nemo enim ipsam voluptatem quia voluptas sit aspernatur aut odit aut fugit,</p>
<a class="abs btn btn-light btn-coach" href="#">READ MORE</a>
<div class="abs coach-photo" role="img" aria-label="Fitness coaches, a woman with dumbbells and a man with a clipboard"></div>
<svg class="abs" style="left:0;top:1630px" width="1200" height="52" viewBox="0 0 1200 52">
  <polygon points="0,0 290,50 0,52" fill="#8dc63f"/>
</svg>

<!-- Services -->
<section class="abs services"></section>
<h2 class="abs section-title serv-title">SERVICES</h2>
<div class="abs serv" style="left:97px"><div class="serv-img" role="img" aria-label="Fresh vegetables and raw meat" style="background:radial-gradient(circle,#c0574a,#5f8d3a)"></div><div class="serv-label">NUTRITION<br>SERVICES</div></div>
<div class="abs serv" style="left:450px"><div class="serv-img" role="img" aria-label="Athlete training with dumbbells" style="background:radial-gradient(circle,#9b7a66,#3a3431)"></div><div class="serv-label">FITNESS<br>SERVICES</div></div>
<div class="abs serv" style="left:802px"><div class="serv-img" role="img" aria-label="Client video call with a coach on a laptop" style="background:radial-gradient(circle,#e9d8b2,#6fa8a3)"></div><div class="serv-label">MOBILE AND ONLINE<br>SERVICES</div></div>

<!-- Testimonial -->
<svg class="abs testi" width="1200" height="560" viewBox="0 0 1200 560">
  <defs>
    <linearGradient id="tg" x1="0" y1="1" x2="1" y2="0">
      <stop offset="0" stop-color="#1b5f9c"/>
      <stop offset=".55" stop-color="#0a8a7b"/>
      <stop offset="1" stop-color="#0aad4c"/>
    </linearGradient>
  </defs>
  <polygon points="0,58 1200,0 1200,527 0,527" fill="url(#tg)"/>
  <polygon points="850,50 1200,18 1200,108" fill="#8dc63f"/>
  <polygon points="0,505 1200,527 1200,560 0,560" fill="#1f2a22"/>
  <polygon points="0,520 330,527 0,555" fill="#8dc63f"/>
</svg>
<svg class="abs avatar" viewBox="0 0 124 134" role="img" aria-label="Portrait of client Mara Ellison">
  <polygon points="62,2 120,34 120,100 62,132 4,100 4,34" fill="#fff"/>
  <polygon points="62,8 114,37 114,97 62,126 10,97 10,37" fill="#b98e73"/>
</svg>
<div class="abs t-name">Mara Ellison</div>
<div class="abs t-loc">Portland, OR</div>
<p class="abs t-quote">Aorbi porta libero id ullamcorper nonummy nibh ligula pulvinar metus eget consectetuer augue nisi quis lacus Ut ac mi quis lacus</p>
<svg class="abs" style="left:90px;top:2393px" width="26" height="48" viewBox="0 0 26 48"><polyline points="22,3 4,24 22,45" fill="none" stroke="#fff" stroke-width="3"/></svg>
<svg class="abs" style="left:1080px;top:2393px" width="26" height="48" viewBox="0 0 26 48"><polyline points="4,3 22,24 4,45" fill="none" stroke="#fff" stroke-width="3"/></svg>
<div class="abs dots"><span class="on"></span><span></span><span></span><span></span><span></span></div>

<!-- Booking -->
<section class="abs book" role="img" aria-label="Wooden table with crackers, almonds, dumbbells and a water bottle" style="top:2640px;height:539px"></section>
<h2 class="abs section-title book-title">BOOK NOW</h2>
<form class="abs form">
  <div class="field">NAME</div>
  <div class="field">DATE
    <svg width="14" height="14" viewBox="0 0 14 14"><rect x="1" y="2" width="12" height="11" fill="none" stroke="#fff" stroke-width="1.4"/><line x1="1" y1="5.5" x2="13" y2="5.5" stroke="#fff" stroke-width="1.4"/></svg>
  </div>
  <div class="field">TIME
    <svg width="14" height="14" viewBox="0 0 14 14"><circle cx="7" cy="7" r="5.8" fill="none" stroke="#fff" stroke-width="1.4"/><polyline points="7,3.5 7,7 9.5,8.5" fill="none" stroke="#fff" stroke-width="1.4"/></svg>
  </div>
  <div class="field msg">MESSAGE</div>
  <span class="submit">SUBMIT</span>
</form>
<div class="abs contact">
  <h3>CONTACT US</h3>
  <div class="c-label">ADDRESS</div><div class="c-val">42 Harbour Lane, Sydney 2000</div>
  <div class="c-label" style="margin-top:24px">PHONE NUMBER</div><div class="c-val">(555) 010 2040</div>
  <div class="c-label" style="margin-top:24px">EMAIL US</div><div class="c-val">INFO@VITALPEAK.EXAMPLE</div>
  <div class="c-label" style="margin-top:24px">FOLLOW US</div>
  <div class="social"><span aria-label="Social link"></span><span aria-label="Social link"></span><span aria-label="Social link"></span><span aria-label="Social link"></span></div>
</div>

<!-- Footer -->
<footer class="abs footer"><p>© 2019 Vital Peak Nutritional Therapy.  All right reserved</p></footer>

</body>
</html>
```